Presentation Folder with inside Pockets

We need a Presentation Folder with inside pockets. The size of the folder will be 9" x 12" and will be printed on the cover, the back and the inside folder flaps. The design will be very simple and consist of our logo (large) on the front cover and our logo (smaller) and contact information on the back. We are open to various colors that you think may go along with our logo. When you display your work, show the front, back and inside.

Target Market(s)

Pharmaceutical Companies

Industry/Entity Type

Work

Requirements
Should not have
• please do not add stock medical photos.

```html
<!DOCTYPE html>
<html lang="en">
<head>
<meta charset="utf-8">
<title>Meridian Trials Inc. – Presentation Folder</title>
<link href="https://fonts.googleapis.com/css2?family=PT+Sans:wght@400;700&display=swap" rel="stylesheet">
<style>
:root{
  --backdrop:#ece9e4;
  --cover-dark:#050505;
  --cover-light:#ffffff;
  --ink:#111111;
  --ink-soft:#444444;
  --on-dark:#e8e8e8;
  --brand-green:#7ab32e;
  --brand-blue:#1f6fae;
  --brand-navy:#1b3f7a;
  --pocket-grey:#e9e9e9;
  --pocket-blue:#2b7dbb;
  --decor-dark:#20281c;
  --decor-light:#f3f4ef;
}
*{margin:0;padding:0;box-sizing:border-box}
html,body{width:1200px;height:993px;overflow:hidden}
body{background:var(--backdrop);font-family:"PT Sans",Arial,sans-serif;position:relative}
.panel{position:absolute;top:38px;height:692px;width:519px;overflow:hidden}
.back-cover{left:75px;background:var(--cover-dark)}
.front-cover{left:594px;background:var(--cover-light)}
.decor-disc{position:absolute;border-radius:50%}
.back-cover .decor-disc{left:110px;top:120px;width:300px;height:300px;background:var(--decor-dark)}
.front-cover .decor-disc{left:45px;top:60px;width:440px;height:440px;background:var(--decor-light)}
.back-contact{position:absolute;left:0;right:0;top:640px;text-align:center;color:var(--on-dark);font-size:13px;line-height:22px}
.back-contact svg{vertical-align:-2px;margin-right:4px}
.brand{position:absolute;display:flex;align-items:center;gap:12px}
.front-cover .brand{left:52px;top:520px}
.brand-dot{border-radius:50%;background:var(--brand-blue);flex:none}
.front-cover .brand-dot{width:66px;height:66px}
.brand-name{font-weight:700;color:var(--ink);text-transform:uppercase;letter-spacing:1px}
.front-cover .brand-name{font-size:28px}
.cover-band{position:absolute;left:0;bottom:0;width:519px;height:60px}
.web{position:absolute;left:0;right:0;bottom:10px;text-align:center;color:#fff;font-size:15px;letter-spacing:3px}
.pockets{position:absolute;left:0;top:730px}
.card{position:absolute;width:203px;height:120px;background:#fff;border:1px solid #bbb;font-size:6.5px;color:var(--ink-soft);padding:12px 10px}
.card-left{left:218px;top:790px}
.card-right{left:779px;top:790px}
.card .brand{position:static;gap:5px}
.card .brand-dot{width:16px;height:16px}
.card .brand-name{font-size:9px;letter-spacing:.3px}
.card-lines{margin-top:26px;line-height:10px}
.card-address{margin-top:8px;line-height:8px}
.card-person{position:absolute;right:30px;top:68px;text-align:center;line-height:8px}
</style>
</head>
<body>
<section class="panel back-cover">
  <div class="decor-disc" role="img" aria-label="Large faint brand emblem decoration"></div>
  <div class="back-contact">
    <div>
      <svg width="11" height="11" viewBox="0 0 24 24"><path fill="#e8e8e8" d="M6.6 10.8a15 15 0 0 0 6.6 6.6l2.2-2.2c.3-.3.7-.4 1-.2 1.1.4 2.3.6 3.6.6.6 0 1 .4 1 1V20c0 .6-.4 1-1 1A17 17 0 0 1 3 4c0-.6.4-1 1-1h3.5c.6 0 1 .4 1 1 0 1.3.2 2.5.6 3.6.1.3 0 .7-.2 1z"/></svg>+1-555-204-7731
      &nbsp;&nbsp;
      <svg width="12" height="10" viewBox="0 0 24 18"><path fill="none" stroke="#e8e8e8" stroke-width="2" d="M1 1h22v16H1zM1 1l11 9 11-9"/></svg>hello@meridiantrials.net
    </div>
    <div>Meridian Trials, Inc. 52 Elm Avenue, Lakeview, NY 11620</div>
  </div>
</section>

<section class="panel front-cover">
  <div class="decor-disc" role="img" aria-label="Large faint brand emblem decoration"></div>
  <div class="brand">
    <span class="brand-dot"></span>
    <span class="brand-name">Meridian Trials Inc.</span>
  </div>
  <svg class="cover-band" viewBox="0 0 519 60" preserveAspectRatio="none">
    <path d="M0 48 Q260 -6 519 38 L519 60 L0 60Z" fill="var(--brand-green)"/>
    <path d="M0 48 Q260 -6 519 38" fill="none" stroke="var(--brand-navy)" stroke-width="3"/>
  </svg>
  <div class="web">www.meridiantrials.net</div>
</section>

<svg class="pockets" width="1200" height="263" viewBox="0 0 1200 263">
  <path d="M30 10 L75 0 L594 0 L570 20 L568 210 Q566 232 545 232 L90 232 Q68 232 68 210 L68 20 L30 20Z" fill="var(--pocket-grey)" stroke="#cfcfcf"/>
  <path d="M594 0 L1113 0 L1160 10 L1160 20 L1130 20 L1130 210 Q1130 232 1108 232 L640 232 Q618 232 616 210 L614 20Z" fill="var(--pocket-blue)"/>
</svg>

<div class="card card-left">
  <div class="brand"><span class="brand-dot"></span><span class="brand-name">Meridian Trials Inc.</span></div>
  <div class="card-lines">+1-555-204-7731<br>hello@meridiantrials.net</div>
  <div class="card-address">Meridian Trials, Inc. 52 Elm Avenue<br>Lakeview, NY 11620</div>
  <div class="card-person">Your Name<br>Title</div>
</div>
<div class="card card-right">
  <div class="brand"><span class="brand-dot"></span><span class="brand-name">Meridian Trials Inc.</span></div>
  <div class="card-lines">+1-555-204-7731<br>hello@meridiantrials.net</div>
  <div class="card-address">Meridian Trials, Inc. 52 Elm Avenue<br>Lakeview, NY 11620</div>
  <div class="card-person">Your Name<br>Title</div>
</div>
</body>
</html>
```